Health and Fitness Club requires a stunning and simple website

We are a health and fitness club based in Dubai, when we launch we will be the biggest club in the country, we will also have the 2 largest activity rooms in the country, we are setting a new standard in the industry by offering one thing, our attitude.

Our attitude means the following:
unlike other clubs we have no hidden charges or fees
our members can join daily, monthly, 6 months or annually
our service and facility are comparable to 5* hotel gyms
our equipment is second to none
our space is the biggest in the country
we do not force our members to use our in-house personal trainers - you can bring your own and we will not charge them entry!
we will have a cutting edge brawnmesh box in our gym with classes by the best trainers in the country
we will be providing free-lance personal trainers a platform to engage customers, grow their business and even use our activity rooms for classes

Basically we will be a gym like no other, simply because we are gym people and we hate the restrictive practices and hidden charges by other gyms, so we are making our own gym which focuses on quality and service.

All of this has to be communicated in the style of the website, the colors of the website we want to be limited to the logo colors as this will be the same theme running throughout the gym.

The landing page of the website HAS to incorporate elements from our social media presences, this basically is the usual, chirplo, snapvault, kinwall. We can have these as a sidebar, the centre of the page should display the latest article from our blog (also on the website) Also we need to have a calendar for activities and classes on the front page. The menu should have links to the following:
Latest News
About us
Team
Gallery
Membership
Classes
Member Log In
Contact Us
Location

The style of the website has to be similar to the logo, particularly in terms of the fonts used.

```html
<!DOCTYPE html>
<html lang="en">
<head>
<meta charset="utf-8">
<title>Apex Fitness</title>
<link href="https://fonts.googleapis.com/css2?family=Open+Sans:wght@400;600;700&display=swap" rel="stylesheet">
<style>
:root{
  --red:#c1141a;
  --red-dark:#9d0d12;
  --ink:#222;
  --muted:#666;
  --panel:#575757;
  --page:#ececec;
  --foot:#2c2c2c;
  --foot-deep:#232323;
  --line:#ddd;
}
*{box-sizing:border-box;margin:0;padding:0}
html,body{width:778px;height:1200px;overflow:hidden}
body{position:relative;font-family:"Open Sans",Arial,sans-serif;color:var(--ink);
  background:radial-gradient(ellipse at 50% 0,#fafafa 0%,var(--page) 70%)}
.abs{position:absolute}
a{color:inherit;text-decoration:none}

/* header */
.brand{left:66px;top:20px;width:92px;height:80px;display:flex;flex-direction:column;align-items:center;justify-content:center;gap:8px}
.brand-mark{width:40px;height:40px;border-radius:50%;background:var(--red)}
.brand-name{font-weight:700;font-size:11px;color:var(--red);letter-spacing:.5px;white-space:nowrap}
.account-btn{top:10px;height:21px;background:#fafafa;border:1px solid #e2e2e2;font-size:9px;display:flex;align-items:center;gap:6px;padding-left:10px;color:#333}
.account-btn i{width:8px;height:10px;background:#333;border-radius:1px;display:block}
.social-top{top:10px;width:16px;height:16px;border-radius:2px}
.phone{left:424px;top:55px;font-size:12.5px;color:#333;display:flex;align-items:center;gap:6px}
.quote-call{left:427px;top:74px;font-size:13px;color:var(--red);font-weight:600}
.search{left:542px;top:59px;width:158px;height:21px;display:flex}
.search span{flex:1;background:#fff;border:1px solid #ccc;font-size:7px;font-style:italic;color:#888;padding:6px 0 0 12px}
.search b{width:26px;background:#111;display:flex;align-items:center;justify-content:center}

/* nav */
.main-nav{left:64px;top:116px;width:643px;height:35px;background:linear-gradient(#d1161d,#a50e13);display:flex;font-size:9.6px;color:#fff}
.main-nav a{flex:1 1 auto;display:flex;align-items:center;justify-content:center;padding:0 6px;white-space:nowrap;border-right:1px solid rgba(255,255,255,.2)}
.main-nav a.active{background:rgba(0,0,0,.15)}
.main-nav a:last-child{border:none}

/* showcase */
.showcase{left:64px;top:151px;width:643px;height:412px;background:var(--panel)}
.hero{left:73px;top:160px;width:627px;height:268px;background:linear-gradient(100deg,#9ea6a8 0%,#c9c3b6 45%,#d7b69e 70%,#e7e2da 100%)}
.hero-caption{left:73px;top:238px;width:250px;height:100px;background:rgba(60,60,60,.72);color:#fff;padding:14px 9px}
.hero-caption h2{font-size:11.5px;font-weight:600;margin-bottom:10px}
.hero-caption p{font-size:8.8px;line-height:13px;text-align:right;color:#eee}
.hero-next{left:670px;top:275px;width:30px;height:30px;background:rgba(70,70,70,.85);display:flex;align-items:center;justify-content:center}
.feature{top:441px;width:196px;height:108px}
.feature .shot{position:absolute;inset:0}
.feature .cap{position:absolute;left:0;right:0;bottom:0;height:34px;background:rgba(40,40,40,.6);color:#fff;padding:3px 8px}
.feature h3{font-size:11.5px;font-weight:400}
.feature p{font-size:7.6px}
.feature .go{position:absolute;right:9px;top:11px;width:11px;height:11px;border:1.5px solid #ddd;border-radius:50%}

/* content */
.content{left:64px;top:563px;width:643px;height:427px;background:#fff}
.section-band{left:65px;top:577px;width:432px;height:23px}
.section-band span{position:absolute;left:10px;top:4px;color:#fff;font-weight:600;font-size:11.5px}
.article-img{left:82px;width:131px;height:80px}
.art-1{background:linear-gradient(120deg,#a7b6c2,#5e86b4 60%,#c9b7a6)}
.art-2{background:linear-gradient(120deg,#c4b2a4,#7fa6c8 60%,#d9d6d2)}
.art-3{background:linear-gradient(120deg,#a9c8e0,#d58aa2 55%,#b9c48a)}
.article-body{left:222px;width:264px}
.article-body h4{font-size:9.6px;font-weight:400;line-height:11.5px;margin-bottom:3px}
.article-body p{font-size:7.4px;line-height:11.8px;color:var(--muted);text-align:justify}
.article-body a{display:block;font-size:7.4px;color:var(--red);margin-top:3px}
.article-meta{left:80px;font-size:7px;color:#666}
.more-btn{left:436px;top:942px;width:55px;height:18px;border:1px solid #e0e0e0;background:#fafafa;font-size:7.8px;font-weight:700;color:var(--red);display:flex;align-items:center;justify-content:center}

/* sidebar */
.side-title{left:532px;font-size:12px;color:var(--red)}
.calendar{left:532px;top:596px;width:156px;height:140px;border:1px solid var(--line);background:#fafafa;padding:4px 8px}
.cal-head{display:flex;justify-content:space-between;font-size:9.4px;color:var(--red);padding:2px 6px;margin-bottom:6px}
.cal-head i{color:#aaa;font-style:normal;font-size:7px}
.calendar table{width:100%;border-collapse:separate;border-spacing:2px 2px;font-size:7.6px;text-align:center}
.calendar th{font-weight:400;color:#888;font-size:7.6px}
.calendar td{border:1px solid #ddd;background:#fff;height:14px;color:#444}
.calendar td.off{color:#ccc}
.calendar td.today{background:var(--red);color:#fff;border-color:var(--red)}
.click-btn{left:533px;top:753px;width:156px;height:24px;background:linear-gradient(#d1161d,#a80e13);color:#fff;font-size:9.6px;font-weight:600;display:flex;align-items:center;justify-content:center;border:1px solid #8a0a0e}
.testimonial{left:530px;top:815px;width:162px;height:71px;border:1px solid var(--line);background:#fff;padding:10px 8px;font-size:7.4px;line-height:11.7px;color:#555;text-align:justify;box-shadow:0 1px 3px rgba(0,0,0,.08)}
.testimonial:after{content:"";position:absolute;left:80px;bottom:-7px;width:12px;height:12px;background:#fff;border-right:1px solid var(--line);border-bottom:1px solid var(--line);transform:rotate(45deg)}
.avatar{left:552px;top:892px;width:49px;height:41px;background:linear-gradient(#cfb7a2,#8f7563)}
.client-name{left:610px;top:904px;font-size:7.8px;color:#1c5d9b}

/* footer */
.footer{left:0;top:1016px;width:778px;height:127px;background:var(--foot)}
.footer-col{top:1026px;color:#eee}
.footer-col h5{font-size:10.6px;font-weight:400;margin-bottom:14px}
.footer-col a{display:block;font-size:8px;line-height:15.6px;padding-left:3px}
.footer-bottom{left:0;top:1143px;width:778px;height:57px;background:var(--foot-deep)}
.social-foot{top:1158px;width:20px;height:20px;border-radius:50%;background:#e4e4e4}
.legal{right:82px;top:1151px;font-size:7.4px;color:#bbb;text-align:right;line-height:15.5px}
</style>
</head>
<body>

<header>
  <div class="abs brand"><span class="brand-mark"></span><span class="brand-name">APEX FITNESS</span></div>
  <a class="abs account-btn" style="left:443px;width:63px"><i></i>Login</a>
  <a class="abs account-btn" style="left:510px;width:78px"><i></i>Register</a>
  <span class="abs social-top" style="left:612px;background:#3b5a96" role="img" aria-label="kinwall"></span>
  <span class="abs social-top" style="left:637px;background:#2aa3d8" role="img" aria-label="chirplo"></span>
  <span class="abs social-top" style="left:661px;background:#1c6fa8" role="img" aria-label="workgrid"></span>
  <span class="abs social-top" style="left:685px;background:#7a6a5b" role="img" aria-label="snapvault"></span>
  <div class="abs phone">
    <svg width="16" height="14" viewBox="0 0 16 14"><path d="M3 1l3 3-2 2c1 2 3 4 5 5l2-2 3 3-2 2C7 14 1 8 1 3z" fill="#555"/></svg>
    03 5520 4410
  </div>
  <div class="abs quote-call">Free Quotes Call</div>
  <div class="abs search"><span>Search</span><b><svg width="12" height="12" viewBox="0 0 12 12"><circle cx="5" cy="5" r="3.6" stroke="#fff" stroke-width="1.6" fill="none"/><path d="M7.6 7.6L11 11" stroke="#fff" stroke-width="1.8"/></svg></b></div>
</header>

<nav class="abs main-nav">
  <a class="active">Home</a><a>About Us</a><a>Latest News</a><a>Team</a><a>Gallery</a><a>Membership</a><a>Classes</a><a>Member Log In</a><a>Contact Us</a><a>Location</a>
</nav>

<section class="abs showcase"></section>
<div class="abs hero" role="img" aria-label="Smiling woman with a towel training on an exercise bike in the gym"></div>
<div class="abs hero-caption">
  <h2>Integer Purus Commodo Varius&nbsp; Facilisis</h2>
  <p>Sed ut perspiciatis unde omnis iste natus error sit voluptatem accusantium doloremque laudan-tium, totam rem aperiam.natus error sit volupta-</p>
</div>
<div class="abs hero-next"><svg width="10" height="12" viewBox="0 0 10 12"><path d="M2 1l5 5-5 5" stroke="#fff" stroke-width="2.4" fill="none"/></svg></div>

<div class="abs feature" style="left:73px">
  <div class="shot" role="img" aria-label="Member smiling during a consultation" style="background:linear-gradient(120deg,#d7d9dc,#9aa0a8)"></div>
  <div class="cap"><h3>Fitness Club</h3><p>we have no hidden charges or fees</p><span class="go"></span></div>
</div>
<div class="abs feature" style="left:287px">
  <div class="shot" role="img" aria-label="Personal trainer with a towel in the gym" style="background:linear-gradient(120deg,#cfc6ba,#a58b74)"></div>
  <div class="cap"><h3>Personal Trainers</h3><p>Grow their business &amp; even use our activity</p><span class="go"></span></div>
</div>
<div class="abs feature" style="left:502px">
  <div class="shot" role="img" aria-label="Woman lifting weights in a class" style="background:linear-gradient(120deg,#8e9296,#d9d6d2)"></div>
  <div class="cap"><h3>Classes</h3><p>cutting edge brawnmesh box in our gym</p><span class="go"></span></div>
</div>

<main class="abs content"></main>
<div class="abs section-band">
  <svg width="432" height="23" viewBox="0 0 432 23"><polygon points="0,0 426,0 432,23 0,23" fill="#c1141a"/></svg>
  <span>Latest Article</span>
</div>

<div class="abs article-img art-1" style="top:616px" role="img" aria-label="Smiling man in a blue shirt at the gym"></div>
<div class="abs article-body" style="top:617px">
  <h4>Maecenas vitae auctor odio. Praesent gravida urna non nunc ornare mollis.</h4>
  <p>Maecenas vitae auctor odio. Praesent gravida urna non nunc ornare mollis. Morbi nisl dolor, cursus id nisl sit amet, sagittis blandit purus. Integer in rutrum arcu. Nunc consectetur massa mauris, vel tristique tellus tempus vitae.</p>
  <a>Read Full&gt;&gt;</a>
</div>
<div class="abs article-meta" style="top:704px">Views : 3890 &nbsp;|&nbsp; Shares : 499</div>

<div class="abs article-img art-2" style="top:733px" role="img" aria-label="Woman training on a rowing machine with a coach"></div>
<div class="abs article-body" style="top:734px">
  <h4>Maecenas vitae auctor odio. Praesent gravida urna non nunc ornare mollis.</h4>
  <p>Maecenas vitae auctor odio. Praesent gravida urna non nunc ornare mollis. Morbi nisl dolor, cursus id nisl sit amet, sagittis blandit purus. Integer in rutrum arcu. Nunc consectetur massa mauris, vel tristique tellus tempus vitae.</p>
  <a>Read Full&gt;&gt;</a>
</div>
<div class="abs article-meta" style="top:821px">Views : 3890 &nbsp;|&nbsp; Shares : 499</div>

<div class="abs article-img art-3" style="top:851px" role="img" aria-label="Two women stretching outdoors on a track"></div>
<div class="abs article-body" style="top:852px">
  <h4>Maecenas vitae auctor odio. Praesent gravida urna non nunc ornare mollis.</h4>
  <p>Maecenas vitae auctor odio. Praesent gravida urna non nunc ornare mollis. Morbi nisl dolor, cursus id nisl sit amet, sagittis blandit purus. Integer in rutrum arcu. Nunc consectetur massa mauris, vel tristique tellus tempus vitae.</p>
  <a>Read Full&gt;&gt;</a>
</div>
<div class="abs article-meta" style="top:939px">Views : 3890 &nbsp;|&nbsp; Shares : 499</div>
<a class="abs more-btn">MORE</a>

<aside>
  <div class="abs side-title" style="top:573px">Activities and Classes</div>
  <div class="abs calendar">
    <div class="cal-head"><i>«</i>February 2014<i>»</i></div>
    <table>
      <tr><th>Su</th><th>Mo</th><th>Tu</th><th>We</th><th>Th</th><th>Fr</th><th>Sa</th></tr>
      <tr><td class="off">25</td><td class="off">26</td><td class="off">27</td><td class="off">28</td><td class="off">29</td><td class="off">30</td><td>1</td></tr>
      <tr><td>2</td><td>3</td><td>4</td><td>5</td><td>6</td><td>7</td><td>8</td></tr>
      <tr><td>9</td><td>10</td><td>11</td><td>12</td><td>13</td><td>14</td><td>15</td></tr>
      <tr><td>16</td><td>17</td><td>18</td><td>19</td><td>20</td><td class="today">21</td><td>22</td></tr>
      <tr><td>23</td><td>24</td><td>25</td><td>26</td><td>27</td><td>28</td><td>29</td></tr>
      <tr><td>30</td><td class="off">1</td><td class="off">2</td><td class="off">3</td><td class="off">4</td><td class="off">5</td><td class="off">6</td></tr>
    </table>
  </div>
  <a class="abs click-btn">Clickhere &gt;&gt;</a>
  <div class="abs side-title" style="top:792px;left:534px">What Clients Say</div>
  <div class="abs testimonial">Sed ut perspiciatis unde omnis iste natus voluptatem accusantium doloremque laudantium, totam rem aperiam, eaque quae inventore veritatis quasi</div>
  <div class="abs avatar" role="img" aria-label="Client portrait"></div>
  <div class="abs client-name">-- Daniel , Dubai</div>
</aside>

<footer>
  <div class="abs footer"></div>
  <div class="abs footer-col" style="left:66px"><h5>QUICK LINKS</h5><a>Euismod&nbsp; Molestie Vehicula</a><a>Maecenas Nulla Nibh Accumsan</a><a>Cras Vitae Lacus Suscipit</a><a>Curabitur&nbsp; Fringilla&nbsp; Dolor</a><a>Etiam Purus Aliquam Fringilla</a></div>
  <div class="abs footer-col" style="left:229px"><h5>QUICK LINKS</h5><a>Euismod&nbsp; Molestie Vehicula</a><a>Maecenas Nulla Nibh Accumsan</a><a>Cras Vitae Lacus Suscipit</a><a>Curabitur&nbsp; Fringilla&nbsp; Dolor</a><a>Etiam Purus Aliquam Fringilla</a></div>
  <div class="abs footer-col" style="left:405px"><h5>QUICK LINKS</h5><a>Euismod&nbsp; Molestie Vehicula</a><a>Maecenas Nulla Nibh Accumsan</a><a>Cras Vitae Lacus Suscipit</a><a>Curabitur&nbsp; Fringilla&nbsp; Dolor</a><a>Etiam Purus Aliquam Fringilla</a></div>
  <div class="abs footer-col" style="left:580px"><h5>QUICK LINKS</h5><a>Euismod&nbsp; Molestie Vehicula</a><a>Maecenas Nulla Nibh Accumsan</a><a>Cras Vitae Lacus Suscipit</a><a>Curabitur&nbsp; Fringilla&nbsp; Dolor</a><a>Etiam Purus Aliquam Fringilla</a></div>
  <div class="abs footer-bottom"></div>
  <span class="abs social-foot" style="left:70px;background:#2f6fc0" role="img" aria-label="kinwall"></span>
  <span class="abs social-foot" style="left:93px" role="img" aria-label="chirplo"></span>
  <span class="abs social-foot" style="left:116px" role="img" aria-label="workgrid"></span>
  <span class="abs social-foot" style="left:139px" role="img" aria-label="plusring"></span>
  <span class="abs social-foot" style="left:162px" role="img" aria-label="clipstream"></span>
  <span class="abs social-foot" style="left:185px" role="img" aria-label="feed"></span>
  <div class="abs legal">Privay&nbsp;|&nbsp;&nbsp; Terms&nbsp;&nbsp;|&nbsp;&nbsp; Contact Us<br>© 2014 apex-fitness, All Rights Reserved</div>
</footer>

</body>
</html>
```